Business card for marketing analytics company

Need a business card for new company. I have a logo already that I want to be built into the card and should use those colours

Company is called steered by tallies
Design must bring steered by tallies to life not be a card that could be for anyone with a logo put on it.

Like the front to be fairly clean and uncluttered bringing the logo out with a suitable design on the back of the card.

The logo represents a compass and business growth so those themes along with numbers, analytics , data are appropriate.
I'm often working with creative industries so also needs to reflect the creative side of analytics rather than be very corporate looking.

Target Market(s)

Ad agency, media agency, consumer goods clients

Industry/Entity Type

Market Research

Contact Information for Business Card

Needs to include name, title, email and phone number

Colors
f78f20
f68d4d
ec1f27

Requirements
Must have
• Must bring steered by tallies to life not be a card that could be for anyone with a logo put on it.
• Logo, Correct colours
• Like a design on the back that relates to company name
• Designs for both sides
Should not have
• Please do not just submit logo and a coloured card.
• It needs to have a design element to it
• No black background
• No clear cards - needs front & back

```html
<!DOCTYPE html>
<html lang="en">
<head>
<meta charset="utf-8">
<title>Steered by Tallies – Business Card</title>
<link href="https://fonts.googleapis.com/css2?family=Lato:wght@400;700&display=swap" rel="stylesheet">
<style>
  :root {
    --backdrop: #2f2f31;
    --card-white: #ffffff;
    --brand-red: #c01b22;
    --brand-orange: #f37021;
    --accent-orange: #f78f20;
    --slate: #4f5a62;
    --text-light: #ffffff;
  }
  * { margin: 0; padding: 0; box-sizing: border-box; }
  html, body {
    width: 1200px;
    height: 987px;
    overflow: hidden;
    background: var(--backdrop);
    font-family: "Lato", sans-serif;
  }
  .card {
    position: absolute;
    left: 293px;
    width: 615px;
    height: 351px;
    border-radius: 20px;
    overflow: hidden;
  }
  .card--front { top: 130px; background: var(--card-white); }
  .card--back { top: 505px; background: var(--brand-orange); }
  .card__art { position: absolute; inset: 0; width: 100%; height: 100%; }

  .brand {
    position: absolute;
    left: 162px;
    top: 46px;
    display: flex;
    align-items: center;
    gap: 18px;
  }
  .brand__dot {
    width: 100px;
    height: 100px;
    border-radius: 50%;
    border: 3px solid var(--brand-red);
  }
  .brand__name {
    font-size: 30px;
    font-weight: 400;
    color: var(--slate);
    line-height: 1;
  }

  .holder {
    position: absolute;
    right: 354px;
    top: 254px;
    text-align: right;
    color: var(--text-light);
  }
  .holder__name {
    font-size: 23px;
    font-weight: 700;
    letter-spacing: 0.5px;
    line-height: 1.1;
    text-transform: uppercase;
  }
  .holder__title { font-size: 17px; font-weight: 700; margin-top: 3px; }

  .divider {
    position: absolute;
    left: 285px;
    top: 243px;
    width: 1px;
    height: 72px;
    background: var(--text-light);
  }

  .contact {
    position: absolute;
    left: 306px;
    top: 243px;
    list-style: none;
    color: var(--text-light);
    font-size: 17px;
    line-height: 24px;
  }

  .back-brand {
    position: absolute;
    left: 308px;
    right: 0;
    top: 172px;
    display: flex;
    flex-direction: column;
    align-items: center;
    gap: 10px;
    color: var(--text-light);
  }
  .back-brand__dot {
    width: 70px;
    height: 70px;
    border-radius: 50%;
    border: 3px solid var(--text-light);
  }
  .back-brand__name { font-size: 21px; font-weight: 400; line-height: 1; }
  .back-url {
    position: absolute;
    left: 308px;
    right: 0;
    top: 300px;
    text-align: center;
    color: var(--text-light);
    font-size: 16px;
  }
</style>
</head>
<body>
  <section class="card card--front">
    <svg class="card__art" viewBox="0 0 615 351" preserveAspectRatio="none" aria-hidden="true">
      <path d="M0 180 Q307 230 615 180 L615 351 L0 351 Z" fill="var(--brand-red)"/>
      <path d="M40 183 Q307 210 570 181" fill="none" stroke="var(--slate)" stroke-width="3"/>
      <path d="M50 187 Q307 218 560 184" fill="none" stroke="var(--accent-orange)" stroke-width="3"/>
      <path d="M70 190 Q307 220 545 188" fill="none" stroke="var(--card-white)" stroke-width="1.5"/>
    </svg>
    <div class="brand">
      <span class="brand__dot"></span>
      <span class="brand__name">Steered by Tallies</span>
    </div>
    <div class="holder">
      <p class="holder__name">Dana Holt</p>
      <p class="holder__title">CEO/Founder</p>
    </div>
    <span class="divider"></span>
    <ul class="contact">
      <li>Phone : 555 210 4837</li>
      <li>dana@steeredbytallies.com</li>
      <li>www.steeredbytallies.com</li>
    </ul>
  </section>

  <section class="card card--back">
    <svg class="card__art" viewBox="0 0 615 351" preserveAspectRatio="none" aria-hidden="true">
      <!-- tally groups rising like a growth chart -->
      <g class="tallies" stroke="var(--text-light)" stroke-width="4" stroke-linecap="round" opacity="0.35">
        <path d="M48 150 V190 M60 150 V190 M72 150 V190 M84 150 V190 M40 184 L94 156"/>
        <path d="M118 120 V190 M130 120 V190 M142 120 V190 M154 120 V190 M110 180 L164 130"/>
        <path d="M188 80 V190 M200 80 V190 M212 80 V190 M224 80 V190 M180 172 L234 98"/>
      </g>
      <!-- sweeping bands echoing the front -->
      <path d="M0 260 Q180 225 300 351 L0 351 Z" fill="var(--brand-red)"/>
      <path d="M0 250 Q190 212 318 351" fill="none" stroke="var(--slate)" stroke-width="3"/>
      <path d="M0 242 Q200 200 336 351" fill="none" stroke="var(--text-light)" stroke-width="1.5"/>
    </svg>
    <div class="back-brand">
      <span class="back-brand__dot"></span>
      <span class="back-brand__name">Steered by Tallies</span>
    </div>
    <p class="back-url">www.steeredbytallies.com</p>
  </section>
</body>
</html>
```